A4 Tri-fold Brochure for Sedation Dentist Specialist Dr. Marlon and Sedation Dentistry.

I would like to create an A4 tri-fold brochure for our Dental Sedation Specialist Dr. Marlon Duque. Please carefully select the most suitable highlights from his bio below.

This brochure has two parts. Highlighting what makes Dr. Marlon Duque unique and trustworthy. Include a picture of him (attached). The second part is about sedation dentistry. All you need to know here: http://www.calmchairhub.example/what-is-calm-chair-care

Avoid making it too wordy.

Meet Dr. Roel Benet Marlon Duque, DDS

Inspired to Become a Dentist:
As a child, Dr. Marlon Duque always felt stressed whenever he had to see a dentist. He knew that he wanted to become a dentist to help put patients completely at ease while they experienced quality dental care.

He is passionate about giving patients the healthy, beautiful smiles they deserve. “I find it fulfilling when I can see my patients’ beautiful smiles and how they can finally appreciate the joy of eating with a healthy set of teeth. However, what I love most about my job is the ability to provide a stress-free and comfortable experience at the dentist’s office, particularly for children, through sedation and general anesthesia.”

Educational Achievements:
Before becoming a dentist, Dr. Marlon Duque earned his undergraduate degree at the Northvale Institute of Arts where he received a Bachelor of Medical Science Honor Specialization degree with distinction in biochemistry. He then completed his Doctor of Dental Surgery degree with honors at the Kestrel Bay College. While there, he received the Linnet Orr Award in his class for outstanding achievement in anesthesia. He then pursued his three-year residency as well as a master’s degree in dental anesthesia at the Kestrel Bay College.

So he can provide his patients with the latest in dentistry, Dr. Marlon Duque enjoys pursuing additional knowledge, particularly in the areas of dental anesthesia as well as advanced technologies in dentistry. He is currently part of the Bright Arc study circle and has enrolled in the Core Anchor Short- Fellowship Course. He also serves as a clinical instructor at the Halvex Wing at the Kestrel Bay College.

Association Memberships:
In addition to his academic credentials, Dr. Marlon Duque is a member of several associations:
The Fenwick Board of Oral Practitioners of Ontario (FBOPO)
Dental Meridian Guild of Oral Sleep Care (MGOSC)
Northern Circle of Oral Calm Care (NCOCC)
Pellham Dental Alliance (PDA)
Outside the Practice

When he’s not at the practice, Dr. Marlon Duque enjoys spending time with his wife Dorla and their two poodles Pippa and Bramble, who are spoiled rotten! “Dorla and I love taking our dogs out on hikes and to the dog park on weekends. I also enjoy a wide range of activities from model building and playing the piano to soccer, gym and archery.” He stays fit by working out at the local Fitwell gym, and he likes to walk in Marrow Creek Park and Ashbury Field Park.

Dr. Marlon Duque considers himself to be a kid at heart. He is a big fan of superheroes and animated movies. “I get really excited about any upcoming superhero or Vellum Spark movies. Till this day, I still collect superhero toy figures.”

He supports the BrightWard Fund as well as the Lakeshore League for Animal Welfare and Rescue (LLAWR).

Experience outstanding dental care with our highly skilled dentist. Contact us today to schedule an appointment with Dr. Marlon Duque! He speaks English, Cantonese, and Mandarin.

Target Market(s)

Mothers with young kids.

Industry/Entity Type

Dental

Font styles to use
Sans Serif

Requirements
Should not have
• Prices

```html
<!DOCTYPE html>
<html lang="en">
<head>
<meta charset="utf-8">
<title>Dr. Marlon Duque – Tri-fold Brochure Inside</title>
<link href="https://fonts.googleapis.com/css2?family=Open+Sans:wght@400;600;700&display=swap" rel="stylesheet">
<style>
  :root {
    --bg: #2b2b2b;
    --paper: #f4f6f8;
    --blue: #1b7fc9;
    --blue-deep: #0e5f9e;
    --blue-light: #4fa8dc;
    --green: #4fcf8f;
    --green-deep: #34b979;
    --ink: #2a2f36;
    --photo-doc-a: #8b8f96;
    --photo-doc-b: #d9dde2;
  }
  * { box-sizing: border-box; margin: 0; padding: 0; }
  html, body { width: 1200px; height: 800px; overflow: hidden; background: var(--bg); }
  body { font-family: "Open Sans", Arial, sans-serif; color: var(--ink); }

  .brochure {
    position: absolute; left: 50px; top: 11px;
    width: 1100px; height: 778px;
    background: linear-gradient(90deg, #eef1f4 0%, #f7f9fb 45%, #e9eef2 100%);
    overflow: hidden;
  }
  .panel { position: absolute; top: 0; height: 100%; width: 366.67px; }
  .panel--left { left: 0; }
  .panel--middle { left: 366.67px; }
  .panel--right { left: 733.33px; }

  .doctor-photo {
    position: absolute; left: 0; top: 0; width: 366.67px; height: 600px;
    background: linear-gradient(160deg, var(--photo-doc-b) 0%, var(--photo-doc-a) 60%, #3d4d66 100%);
  }
  .clinic-wash {
    position: absolute; left: 366.67px; top: 0; width: 733.33px; height: 620px;
    background: linear-gradient(180deg, rgba(200,210,222,0.25) 0%, rgba(170,190,210,0.35) 100%);
  }

  .bottom-band { position: absolute; left: 0; bottom: 0; width: 1100px; height: 260px; }

  .photo-circle {
    position: absolute; border-radius: 50%;
    border: 8px solid var(--blue-light);
    box-shadow: 0 0 0 4px #fff inset;
  }
  .photo-circle--clinic {
    left: 110px; top: 500px; width: 260px; height: 240px;
    background: linear-gradient(135deg, #e7edf3 0%, #9fb5c9 55%, #2c4f8f 100%);
  }
  .photo-circle--smile {
    left: 930px; top: 545px; width: 150px; height: 150px;
    background: linear-gradient(135deg, #f3e6dc 0%, #d9b8a0 60%, #b89a85 100%);
  }

  .content { position: absolute; top: 40px; left: 34px; right: 28px; }
  .eyebrow { color: var(--blue); font-weight: 600; font-size: 17px; letter-spacing: 0.5px; text-transform: uppercase; line-height: 1.1; }
  .heading { color: var(--blue-deep); font-weight: 700; font-size: 30px; text-transform: uppercase; line-height: 1.05; margin-bottom: 16px; }
  .body-text { font-size: 11px; line-height: 1.5; text-align: justify; margin-bottom: 12px; }

  .doctor-name { margin-top: 20px; color: var(--blue-light); font-size: 19px; font-weight: 400; text-transform: uppercase; line-height: 1.25; }
  .doctor-title { color: var(--blue-deep); font-weight: 700; font-size: 19px; text-align: right; }

  .website {
    position: absolute; left: 366.67px; width: 366.67px; bottom: 44px;
    color: #fff; font-size: 15px; font-weight: 600; text-align: center;
    display: flex; align-items: center; justify-content: center; gap: 8px;
  }
  .website svg { width: 14px; height: 14px; }
</style>
</head>
<body>
  <main class="brochure">
    <div class="doctor-photo" role="img" aria-label="Portrait of Dr. Marlon Duque smiling in navy scrubs with a stethoscope"></div>
    <div class="clinic-wash" role="img" aria-label="Soft faded background of a patient relaxing in a dental chair"></div>

    <svg class="bottom-band" viewBox="0 0 1100 260" preserveAspectRatio="none" aria-hidden="true">
      <path d="M0 100 C180 110 300 120 380 150 C470 175 560 150 650 130 C800 95 950 70 1100 30 L1100 260 L0 260 Z" fill="var(--blue)"/>
      <path d="M0 122 C180 132 300 140 380 170 C470 195 560 170 650 150 C800 115 950 90 1100 52 L1100 260 L0 260 Z" fill="#fff"/>
      <path d="M0 132 C180 142 300 150 380 180 C470 205 560 180 650 160 C800 125 950 100 1100 62 L1100 260 L0 260 Z" fill="var(--green)"/>
      <path d="M0 230 C300 220 600 245 1100 210 L1100 260 L0 260 Z" fill="var(--green-deep)" opacity="0.35"/>
    </svg>

    <div class="photo-circle photo-circle--clinic" role="img" aria-label="Dentist in a mask examining a young patient in a dental chair"></div>
    <div class="photo-circle photo-circle--smile" role="img" aria-label="Close-up of a smiling woman with healthy teeth"></div>

    <section class="panel panel--middle">
      <div class="content">
        <p class="eyebrow">Educational</p>
        <h2 class="heading">Achievements</h2>
        <p class="body-text">Before becoming a dentist, Dr. Marlon Duque earned his undergraduate degree at the Northvale Institute of Arts where he received a Bachelor of Medical Science Honor Specialization degree with distinction in biochemistry. He then completed his Doctor of Dental Surgery degree with honors at the Kestrel Bay College. While there, he received the Linnet Orr Award in his class for outstanding achievement in anesthesia. He then pursued his three-year residency as well as a master’s degree in dental anesthesia at the Kestrel Bay College.</p>
        <p class="body-text">So he can provide his patients with the latest in dentistry, Dr. Marlon Duque enjoys pursuing additional knowledge, particularly in the areas of dental anesthesia as well as advanced technologies in dentistry. He is currently part of the Bright Arc study circle and has enrolled in the Core Anchor Short- Fellowship Course. He also serves as a clinical instructor at the Halvex Wing at the Kestrel Bay College.</p>
        <p class="doctor-name">Dr. Roel Benet Marlon Duque</p>
        <p class="doctor-title">DDS</p>
      </div>
    </section>

    <section class="panel panel--right">
      <div class="content">
        <p class="eyebrow">Outside</p>
        <h2 class="heading">The Practice</h2>
        <p class="body-text">When he’s not at the practice, Dr. Marlon Duque enjoys spending time with his wife Dorla and their two poodles Pippa and Bramble, who are spoiled rotten! “Dorla and I love taking our dogs out on hikes and to the dog park on weekends. I also enjoy a wide range of activities from model building and playing the piano to soccer, gym and archery.” He stays fit by working out at the local Fitwell gym, and he likes to walk in Marrow Creek Park and Ashbury Field Park.</p>
        <p class="body-text">Dr. Marlon Duque considers himself to be a kid at heart. He is a big fan of superheroes and animated movies. “I get really excited about any upcoming superhero or Vellum Spark movies. Till this day, I still collect superhero toy figures.”</p>
        <p class="body-text">He supports the BrightWard Fund as well as the Lakeshore League for Animal Welfare and Rescue (LLAWR).</p>
        <p class="body-text">Experience outstanding dental care with our highly skilled dentist. Contact us today to schedule an appointment with Dr. Marlon Duque! He speaks English, Cantonese, and Mandarin.</p>
      </div>
    </section>

    <p class="website">
      <svg viewBox="0 0 14 14" aria-hidden="true"><circle cx="7" cy="7" r="6" fill="none" stroke="#fff" stroke-width="1.4"/><path d="M1 7h12M7 1c2.5 3 2.5 9 0 12M7 1c-2.5 3-2.5 9 0 12" fill="none" stroke="#fff" stroke-width="1.1"/></svg>
      www.calmchairdental.example
    </p>
  </main>
</body>
</html>
```